Market place for used airplanes/helicopters/parts

http://www.vingtorget.se needs a facelift.

# What is it
Classifieds for used airplanes/helicopters/parts/spare parts/aviation literature, for people in Scandinavia. The number of classifieds is ~120-200. They are mainly in Swedish, English, Norwegian.

It's not a glamorous or luxurious business, but more for people with a genuine interest in flying, technical things.

Similar to sites like this, but they have much more classifieds than my site
http://www.skyvendor.com/list/list.aspx?ETID=1&setype=1&catid=6
http://www.lindqvistflyg.com/planes.asp?meny=1&typ=single
https://www.hangarhub.com/cat.php?mode=listing&main=

# What I want
Design only - no code. I want a modern, maybe a bit bootstrap like, clean, simple, not flashy, web design. I want the design to be in English.

# Audience of the website
Aviation interested men, 45-65 years old, in the nordic countries (around Sweden).

# Logotype that could be used (but not necessarily)
http://www.vingtorget.se/flygplan_till_salu_large.jpg
http://www.vingtorget.se/flygplan_till_salu.eps

Reason: I decided to extend the deadline with 1 day. The reason is that I (unfortunately) managed to put the contest in the wrong category for 1 day + I want to give you all feedback (been too busy the whole day, sorry).

Hi all! 

Thanks everyone for the contributions you made. 

I will setup a poll for the designs that I like most. Will get back when I have more information. 

Thanks and have a nice weekend!
Erik

Target Market(s)

45-65 old Scandinavian men

Industry/Entity Type

Business

Requirements
Must have
• - A list with classifieds on the first page, so the visitor easily can see new classifieds.
- A classifieds should be able to have more than one photo
- A simple navigation for showing classifieds from categories like airplanes, helicopters/gyrocopters, parts, literature, misc (maybe other categories) .... but still, it's just 100-200 ads so it's not needed that much filtration.

- A placeholder/way of showing aviation news/clips. In the old design I had, it was a column to the right. It's enough to show maybe 2-5 placeholders.
- A placeholder for PlaceMint ads somewhere on the site.
Should not have
• - Carousels
- Too much clutter

```html
<!DOCTYPE html>
<html lang="en">
<head>
<meta charset="utf-8">
<title>Vingtorget – Aircraft for Sale</title>
<link href="https://fonts.googleapis.com/css2?family=Ubuntu:wght@300;400&display=swap" rel="stylesheet">
<style>
:root{
  --blue:#0b5cb0;
  --blue-dark:#063f87;
  --blue-light:#1a7fd6;
  --title:#1b4f8c;
  --text:#555;
  --line:#dcdcdc;
  --news-head:#5cb8ec;
  --btn:#1c8fe0;
  --bg:#fff;
}
*{box-sizing:border-box;margin:0;padding:0}
html,body{width:1072px;height:1200px;overflow:hidden;background:var(--bg);font-family:"Ubuntu",sans-serif;font-weight:300;color:var(--text)}
.page{position:relative;width:1072px;height:1200px;background:linear-gradient(#fff 0,#f1f1f1 150px,#fff 150px)}
.brand{position:absolute;left:71px;top:22px;width:236px;height:88px;display:flex;align-items:center;gap:10px}
.brand-mark{width:22px;height:22px;background:var(--blue-light)}
.brand-name{font-size:34px;font-weight:400;color:var(--blue-dark)}
.social{position:absolute;right:72px;top:88px;display:flex;gap:8px}
.social span{width:24px;height:24px;display:block}
.social .s1{background:#3b5b98}.social .s2{background:#4ab3e8}.social .s3{background:#1780b3}.social .s4{background:#f08a1c}
.nav{position:absolute;left:71px;top:125px;width:932px;height:50px;background:linear-gradient(var(--blue-light),var(--blue-dark));border-radius:3px;display:flex;box-shadow:0 1px 2px rgba(0,0,0,.3)}
.nav a{color:#fff;text-decoration:none;font-size:17px;padding:0 19px;line-height:50px;border-right:1px solid rgba(0,0,0,.25);box-shadow:1px 0 0 rgba(255,255,255,.15)}
.nav a.active{background:var(--blue);padding:0 21px 0 35px}
.main{position:absolute;left:71px;top:212px;width:637px}
.hero-title{font-size:29px;font-weight:400;color:var(--title);margin-left:4px}
.hero-sub{font-size:16px;color:#666;margin:10px 0 0 4px}
.hero-text{font-size:12px;line-height:20px;color:#888;margin:8px 0 0 4px}
.section-title{font-size:23px;font-weight:300;color:#333;margin-top:38px}
.products{margin-top:10px;border:1px solid var(--line);border-radius:3px}
.product{display:flex;height:167px;padding:17px 16px 0;border-bottom:1px solid var(--line);background:linear-gradient(#fff 60%,#f3f3f3)}
.product:last-child{border-bottom:0}
.photo-main{width:164px;height:132px}
.photo-stack{display:flex;flex-direction:column;gap:3px;margin-left:4px}
.photo-stack div{width:94px;height:65px}
.info{margin-left:13px;width:350px}
.info h3{font-size:20px;font-weight:300;color:#333}
.info .lead{font-size:14px;line-height:20px;color:#777;margin-top:5px;white-space:nowrap}
.info .meta{font-size:12px;line-height:20px;color:#888;margin-top:2px;white-space:nowrap}
.btn{display:inline-block;margin-top:6px;background:linear-gradient(#31a4ef,var(--btn));color:#fff;font-size:11px;font-weight:400;padding:0 15px;line-height:24px;border-radius:2px;border:1px solid #1579c2}
.sidebar{position:absolute;left:745px;top:202px;width:257px}
.news{border:1px solid var(--line);border-radius:3px;background:#fff}
.news-head{background:linear-gradient(#7ccaf3,var(--news-head));color:#fff;font-size:19px;font-weight:400;padding:0 23px;line-height:41px;border-radius:3px 3px 0 0}
.news-item{padding:14px 24px 8px;border-bottom:1px solid #e6e6e6}
.news-item:last-child{border-bottom:0;padding-bottom:18px}
.news-item h4{font-size:13px;font-weight:400;color:#444}
.news-item p{font-size:11px;line-height:16px;color:#999;margin-top:2px}
.ad{width:256px}
.ad-one{margin-top:5px;height:198px;background:linear-gradient(135deg,#0d2d6b,#1d4aa6 55%,#dfe6f1)}
.ad-two{margin-top:14px;height:216px;background:linear-gradient(#e5dccd,#b7261f 45%,#9d1f18)}
.footer{position:absolute;left:0;top:1115px;width:1072px;height:85px;background:linear-gradient(var(--blue),var(--blue-dark));border-top:2px solid #0a3f7c;color:#d9e6f5;font-size:13px}
.copy{position:absolute;left:77px;top:34px}
.fnav{position:absolute;right:70px;top:33px;font-size:14px;color:#fff}
.fnav a{color:#fff;text-decoration:none}
</style>
</head>
<body>
<div class="page">
  <div class="brand"><span class="brand-mark"></span><span class="brand-name">Vingtorget</span></div>
  <div class="social"><span class="s1"></span><span class="s2"></span><span class="s3"></span><span class="s4"></span></div>
  <nav class="nav">
    <a class="active" href="#">Home</a><a href="#">About</a><a href="#">Airplanes</a><a href="#">Helicopters</a><a href="#">Parts</a><a href="#">Literature</a><a href="#">Misc.</a><a href="#">Contact</a>
  </nav>

  <main class="main">
    <h1 class="hero-title">Aircraft for Sale - the largest market for flights</h1>
    <p class="hero-sub">Duis tincidunt lectus quis dui viverra vestibulum Suspendisse vulputate</p>
    <p class="hero-text">Nulla elementum dui ut augue. Aliquam vehicula mi at mauris. Maecenas placerat, nisl at consequat rhoncus, sem nunc gravida justo, quis eleifend arcu velit quis lacus. Morbi magna magna, tincidunt a, mattis non, imperdiet vitae, tellus</p>
    <h2 class="section-title">Product Lists</h2>
    <div class="products">
      <article class="product">
        <div class="photo-main" role="img" aria-label="Photo collage of a white microlight aircraft and its cockpit" style="background:linear-gradient(#c9d2dc,#6b6b6b 60%,#2e2a25)"></div>
        <div class="photo-stack">
          <div role="img" aria-label="Photo of a yellow seaplane over water" style="background:linear-gradient(#3f86b7,#2a5f86)"></div>
          <div role="img" aria-label="Photo of jet aircraft in flight" style="background:linear-gradient(#c6d6e6,#7d95ad)"></div>
        </div>
        <div class="info">
          <h3>Norrvind NX ULC</h3>
          <p class="lead">A unique UL machine in carbon fiber, it makes it excep-<br>tionally easy. Empty weight 268kg</p>
          <p class="meta">Manuf. 2006, ca.260 hours, always in hangar.<br>Equipped with constant-speed propeller and save screen.</p>
          <span class="btn">LEARN MORE</span>
        </div>
      </article>
      <article class="product">
        <div class="photo-main" role="img" aria-label="Aerial photo of a white aerobatic aircraft over fields" style="background:linear-gradient(160deg,#8a8e95,#b9a7a6 55%,#6d6361)"></div>
        <div class="photo-stack">
          <div role="img" aria-label="Photo of an airliner against the sky" style="background:linear-gradient(#8fa6c2,#d7b7a2)"></div>
          <div role="img" aria-label="Photo of a transport aircraft on the apron" style="background:linear-gradient(#a8b2ba,#58626b)"></div>
        </div>
        <div class="info">
          <h3>Aerobatic Falkvik F-7 Sport</h3>
          <p class="lead">A unique UL machine in carbon fiber, it makes it excep-<br>tionally easy. Empty weight 268kg</p>
          <p class="meta">Manuf. 2006, ca.260 hours, always in hangar.<br>Equipped with constant-speed propeller and save screen.</p>
          <span class="btn">LEARN MORE</span>
        </div>
      </article>
      <article class="product">
        <div class="photo-main" role="img" aria-label="Photo of a floatplane on a river under a bridge" style="background:linear-gradient(#8fa5b4,#4e5f3f 55%,#2f4a44)"></div>
        <div class="photo-stack">
          <div role="img" aria-label="Photo of biplanes in formation" style="background:linear-gradient(#8d97a0,#b8b3a8)"></div>
          <div role="img" aria-label="Photo of a vintage aircraft in flight" style="background:linear-gradient(#a8c4d8,#7f9a6e)"></div>
        </div>
        <div class="info">
          <h3>Tallmark Tern 140 Auto STC</h3>
          <p class="lead">A unique UL machine in carbon fiber, it makes it excep-<br>tionally easy. Empty weight 268kg</p>
          <p class="meta">Manuf. 2006, ca.260 hours, always in hangar.<br>Equipped with constant-speed propeller and save screen.</p>
          <span class="btn">LEARN MORE</span>
        </div>
      </article>
      <article class="product">
        <div class="photo-main" role="img" aria-label="Photo of a floatplane moored at a lakeside dock" style="background:linear-gradient(#8ea1bd,#3c4d39 55%,#a8b2c0)"></div>
        <div class="photo-stack">
          <div role="img" aria-label="Photo of a bomber aircraft in a sepia sky" style="background:linear-gradient(#d8d3b4,#b5ab86)"></div>
          <div role="img" aria-label="Photo of a flying boat at sunset" style="background:linear-gradient(#8b8a86,#3a3937)"></div>
        </div>
        <div class="info">
          <h3>Sjöberg Loom 6 -82/89</h3>
          <p class="lead">A unique UL machine in carbon fiber, it makes it excep-<br>tionally easy. Empty weight 268kg</p>
          <p class="meta">Manuf. 2006, ca.260 hours, always in hangar.<br>Equipped with constant-speed propeller and save screen.</p>
          <span class="btn">LEARN MORE</span>
        </div>
      </article>
    </div>
  </main>

  <aside class="sidebar">
    <section class="news">
      <h2 class="news-head">LATEST NEWS</h2>
      <div class="news-item"><h4>Duis tincidunt lectus</h4><p>Suspendisse vulputate aliquam dui. Nulla elementum dui ut augue Aliquam ▸</p></div>
      <div class="news-item"><h4>Etiam est nunc venenatis</h4><p>Suspendisse vulputate aliquam dui. Nulla elementum dui ut augue Aliquam ▸</p></div>
      <div class="news-item"><h4>Vivamus porttitor</h4><p>Suspendisse vulputate aliquam dui. ▸</p></div>
      <div class="news-item"><h4>Duis tincidunt lectus</h4><p>Suspendisse vulputate aliquam dui. Nulla elementum dui ut augue Aliquam ▸</p></div>
    </section>
    <div class="ad ad-one" role="img" aria-label="Banner advertisement placeholder"></div>
    <div class="ad ad-two" role="img" aria-label="Banner advertisement placeholder"></div>
  </aside>

  <footer class="footer">
    <p class="copy">© 2013 Company Name.&nbsp; All right reserved.&nbsp; Term of Use</p>
    <p class="fnav"><a href="#">Home</a> &nbsp;/&nbsp; <a href="#">About</a> &nbsp;/&nbsp; <a href="#">Airplanes</a> &nbsp;/&nbsp; <a href="#">Helicopters</a> &nbsp;/&nbsp; <a href="#">Parts</a> &nbsp;/&nbsp; <a href="#">Literature</a> &nbsp;/&nbsp; <a href="#">Misc.</a> &nbsp;/&nbsp; <a href="#">Contact</a></p>
  </footer>
</div>
</body>
</html>
```